Tin Lanterns at Dawn How a City's Most Notorious Nightclub Found a New Calling.

This compelling story deserves a great cover which conveys transformation. As a pastor, I started a church in the financial district of Atlanta. What began as a typical "church plant" became an adventure in risk, creativity, and the building was a beautiful metaphor of transformation as we took a closed down strip club and turned it into a church venue. Our group learned many lessons about accepting people from all sorts of backgrounds, and about seeing God's power at work. I envision a cover which communicates transformation, perhaps using darkness and light, or maybe using the Harbor Lounge building being painted. It was a solid black building (with gold trim) and we painted it white, with a blue logo of the church name. I need book cover, spine, and back, along with whatever is needed for Quillmart to accept it for their site.

```html
<!DOCTYPE html>
<html lang="en">
<head>
<meta charset="utf-8">
<title>Tin Lanterns at Dawn — Book Cover</title>
<link rel="stylesheet" href="https://fonts.googleapis.com/css2?family=Cinzel:wght@400;500;600&family=Oswald:wght@500&display=swap">
<style>
  :root {
    --backdrop: #1e1e1e;
    --cover-black: #050505;
    --gold: #c9b07a;
    --gold-light: #ead8a8;
    --gold-deep: #8f7746;
    --beam-core: #fff9e6;
    --beam-warm: #f2d487;
    --white: #ffffff;
    --bench-wood: #5a2f22;
  }
  * { box-sizing: border-box; margin: 0; padding: 0; }
  html, body {
    width: 1200px; height: 1200px; overflow: hidden;
    background: var(--backdrop);
  }
  .cover {
    position: absolute; left: 210px; top: 12px;
    width: 780px; height: 1176px;
    background: var(--cover-black);
    overflow: hidden;
  }
  .church-scene {
    position: absolute; left: 426px; top: 228px;
    width: 354px; height: 432px;
    background: radial-gradient(ellipse at 60% 50%, rgba(70,70,70,0.6), rgba(35,35,35,0.35) 50%, rgba(5,5,5,0) 78%);
  }
  .light-beam {
    position: absolute; left: 240px; top: 0;
    width: 114px; height: 860px;
    background: linear-gradient(90deg, rgba(242,212,135,0) 0%, rgba(242,212,135,0.6) 20%, var(--beam-core) 42%, var(--beam-core) 58%, rgba(242,212,135,0.6) 80%, rgba(242,212,135,0) 100%);
    filter: blur(5px);
  }
  .light-burst {
    position: absolute; left: 110px; top: 744px;
    width: 380px; height: 240px;
    background: radial-gradient(ellipse at 50% 50%, var(--beam-core) 0%, rgba(242,212,135,0.85) 18%, rgba(201,176,122,0.35) 42%, rgba(5,5,5,0) 70%);
  }
  .pew {
    position: absolute; left: 258px; top: 822px;
    width: 90px; height: 90px;
    background: linear-gradient(180deg, #6b3a2a, var(--bench-wood));
    border-radius: 3px;
  }
  .title { position: absolute; left: 0; top: 0; width: 100%; font-family: "Cinzel", serif; font-weight: 400; }
  .title span { position: absolute; line-height: 1; text-align: center; }
  .title-tin {
    left: 374px; top: 92px; width: 284px;
    font-size: 100px; color: var(--gold); letter-spacing: 4px;
  }
  .title-lanterns {
    left: 40px; top: 265px; width: 680px;
    font-size: 106px; font-weight: 500; letter-spacing: 1px;
    color: var(--cover-black);
    text-shadow:
      2px 0 0 var(--gold), -2px 0 0 var(--gold), 0 2px 0 var(--gold), 0 -2px 0 var(--gold),
      1.5px 1.5px 0 var(--gold), -1.5px 1.5px 0 var(--gold), 1.5px -1.5px 0 var(--gold), -1.5px -1.5px 0 var(--gold);
  }
  .title-at {
    left: 374px; top: 453px; width: 140px;
    font-size: 86px; color: var(--gold); letter-spacing: 2px;
  }
  .title-dawn {
    left: 60px; top: 544px; width: 696px;
    font-size: 198px; font-weight: 500; letter-spacing: 4px;
    background: linear-gradient(180deg, var(--gold-light) 0%, var(--gold) 60%, var(--gold-deep) 100%);
    -webkit-background-clip: text; background-clip: text; color: transparent;
    filter: drop-shadow(0 2px 2px rgba(0,0,0,0.8));
  }
  .subtitle {
    position: absolute; left: 430px; top: 770px;
    font-family: "Oswald", sans-serif; font-weight: 500;
    font-size: 33px; line-height: 1.22; color: var(--white);
  }
  .subtitle .highlight { color: var(--gold); }
  .author {
    position: absolute; left: 0; top: 1041px; width: 780px; text-align: center;
    font-family: "Cinzel", serif; font-weight: 500;
    font-size: 54px; color: var(--white); letter-spacing: 1px;
  }
</style>
</head>
<body>
  <main class="cover">
    <div class="church-scene" role="img" aria-label="Faint photograph of a church building in the darkness"></div>
    <div class="light-beam"></div>
    <div class="light-burst"></div>
    <div class="pew" role="img" aria-label="Wooden church pew standing in the light"></div>

    <h1 class="title">
      <span class="title-tin">TIN</span>
      <span class="title-lanterns">LANTERNS</span>
      <span class="title-at">AT</span>
      <span class="title-dawn">DAWN</span>
    </h1>

    <p class="subtitle">How a City’s Most<br>Notorious Nightclub<br><span class="highlight">Found a New Calling</span></p>

    <p class="author">Author Name</p>
  </main>
</body>
</html>
```